Young, modern, highly skilled carpenter needs business card design

I need a business card design for my construction business. Its called 'Barlow Construction Services'. Im looking for a ultra modern design that incorporates B C S, the first letters of the name with only a subtle reference to carpentry. The design should reflect my high quality work and eye for detail. i have also uploaded some exmaple designs i like.

Industry/Entity Type

Construction

Requirements
Must have
• Name of business, my name, mobile number, ABN number, email address
Nice to have
• A logo incorporating the name of the business

```html
<!DOCTYPE html>
<html lang="en">
<head>
<meta charset="utf-8">
<title>Barlow Construction Services – Business Card</title>
<link rel="stylesheet" href="https://fonts.googleapis.com/css2?family=Carlito:wght@400;700&display=swap">
<style>
  :root {
    --backdrop: #e8ecec;
    --kraft: #c9b25e;
    --kraft-edge: #bfa752;
    --ink: #111111;
  }
  * { margin: 0; padding: 0; box-sizing: border-box; }
  html, body {
    width: 1200px;
    height: 900px;
    overflow: hidden;
    background: var(--backdrop);
    font-family: "Carlito", "Calibri", sans-serif;
    color: var(--ink);
  }
  .canvas {
    position: relative;
    width: 1200px;
    height: 900px;
  }
  .card {
    position: absolute;
    left: 334px;
    width: 544px;
    height: 374px;
    background: radial-gradient(ellipse at 50% 45%, #ccb563 0%, var(--kraft) 60%, var(--kraft-edge) 100%);
  }
  .card--front { top: 60px; }
  .card--back { top: 460px; }

  .front-mark {
    position: absolute;
    left: 0;
    right: 0;
    top: 162px;
    text-align: center;
    font-weight: 700;
    font-size: 68px;
    letter-spacing: 2px;
    line-height: 1;
  }

  .back-name {
    position: absolute;
    left: 64px;
    top: 48px;
    font-weight: 400;
    font-size: 22px;
    letter-spacing: 0.3px;
    line-height: 1;
    white-space: nowrap;
  }

  .contact {
    position: absolute;
    left: 66px;
    top: 222px;
    list-style: none;
    font-size: 20px;
    line-height: 26.5px;
  }
</style>
</head>
<body>
  <main class="canvas">
    <section class="card card--front" aria-label="Card front">
      <div class="front-mark">BCS</div>
    </section>

    <section class="card card--back" aria-label="Card back">
      <div class="back-name">BARLOW CONSTRUCTION SERVICES</div>
      <ul class="contact">
        <li>Liam Barlow</li>
        <li>M: liam_barlow@mailbox.com</li>
        <li>T: 0412583061</li>
        <li>ABN: 47 218 905 364</li>
      </ul>
    </section>
  </main>
</body>
</html>
```